Vernac Law Business cards and stationary design project

We are looking for a stationary design for business cards (double sided), 8x10, 5x7, and legal and standard envelopes.

We would like the design to match the logo that we have already.
Color palate preferred is Teal, White, grey and any others that will look good for a professional law firm.

We would like this statement: "RELATIONSHIPS. RESPECT. RESULT" to be on the back of the business cards and maybe on the stationary if it looks good.

Please see link to website for more information: www.vernac-law.example

Target Market(s)

Potential clients that need Attorney services.

Industry/Entity Type

Law Firm

Contact Information for Business Card

We would like the front and back to be two different colors. Current business cards are teal front, grey back and are a vertical design. We are open to options with colors.

Font styles to use
Serif

Colors
33a6d7
33b8a4
b9b9b9
5c5c5c

Requirements
Must have
• Logo supplied needs to go on the card and stationary.
• Match website color palate, www.vernac-law.example
• Be professional and not too wordy.
• Criminal Law, Civil Litigation, Personal Injury, Restraining Orders need to be on the card.
Nice to have
• RELATIONSHIPS. RESPECT. RESULTS. on the back of the card.
Should not have
• Not be too busy/wordy or too flashy.

```html
<!DOCTYPE html>
<html lang="en">
<head>
<meta charset="utf-8">
<title>Vernac Law – Business Card</title>
<link rel="stylesheet" href="https://fonts.googleapis.com/css2?family=Open+Sans:wght@400;600;700&display=swap">
<style>
  :root {
    --stage: #141414;
    --card-light: #f3f3f3;
    --teal: #137f8c;
    --teal-back: #0d7f8c;
    --ink: #111111;
    --white: #ffffff;
  }
  * { box-sizing: border-box; margin: 0; padding: 0; }
  html, body { width: 1200px; height: 900px; overflow: hidden; }
  body {
    background: var(--stage);
    font-family: "Open Sans", Arial, sans-serif;
    position: relative;
  }
  .card {
    position: absolute;
    top: 184px;
    width: 302px;
    height: 490px;
    border-radius: 14px;
    text-align: center;
  }
  .card--front { left: 299px; background: var(--card-light); color: var(--ink); }
  .card--back { left: 646px; background: var(--teal-back); color: var(--white); }

  .brand-dot {
    position: absolute;
    top: 34px;
    left: 50%;
    width: 82px;
    height: 82px;
    margin-left: -41px;
    border-radius: 50%;
    background: var(--teal);
  }

  .firm-name {
    position: absolute;
    left: 0; right: 0;
    font-family: "Open Sans", Arial, sans-serif;
    font-weight: 600;
    font-size: 30px;
    line-height: 1;
  }
  .card--front .firm-name { top: 141px; color: var(--teal); }
  .card--back .firm-name { top: 282px; color: var(--white); }

  .person { position: absolute; top: 265px; left: 0; right: 0; }
  .person__name { font-weight: 600; font-size: 18px; color: var(--teal); line-height: 1.15; }
  .person__role { font-size: 13.5px; line-height: 1.3; }

  .contacts { position: absolute; top: 331px; left: 0; right: 0; list-style: none; font-size: 13.5px; line-height: 20.5px; }
  .contacts li { display: flex; justify-content: center; align-items: center; gap: 3px; }
  .contacts svg { width: 10px; height: 10px; fill: var(--teal); }

  .address { position: absolute; top: 429px; left: 0; right: 0; font-size: 13px; line-height: 15px; font-style: normal; }

  .practice { position: absolute; top: 369px; left: 0; right: 0; font-weight: 600; font-size: 14.5px; line-height: 20px; }
  .motto { position: absolute; top: 446px; left: 0; right: 0; font-weight: 600; font-size: 14.5px; letter-spacing: 0.1px; }
</style>
</head>
<body>
  <section class="card card--front">
    <span class="brand-dot" aria-hidden="true"></span>
    <h1 class="firm-name">Vernac Law</h1>
    <div class="person">
      <p class="person__name">Daniel Marsh</p>
      <p class="person__role">Managing Director</p>
    </div>
    <ul class="contacts">
      <li><svg viewBox="0 0 10 10"><path d="M2 0.5l1.6 2.2-1 1c.6 1.3 1.5 2.2 2.7 2.7l1-1L8.5 7 7.6 9C4 8.6 1.4 6 1 2.4z"/></svg>(044)-456-7890</li>
      <li><svg viewBox="0 0 10 10"><path d="M3.5 2V1h3v1H9.5v6.5h-9V2zm1-0.2v.2h1v-.2z"/></svg>123-456-7890</li>
      <li><svg viewBox="0 0 10 10"><path d="M0.5 2h9v6h-9z"/></svg>info@youremail.com</li>
      <li><svg viewBox="0 0 10 10"><circle cx="5" cy="5" r="4.5"/></svg>www.website.com</li>
    </ul>
    <address class="address">12345, Address Goes Here<br>Country Name, 123456</address>
  </section>

  <section class="card card--back">
    <h2 class="firm-name">Vernac Law</h2>
    <p class="practice">Practice areas, Criminal Law<br>Civil Litigation/Personal Injury<br>Restraining Orders</p>
    <p class="motto">RELATIONSHIPS. RESPECT. RESULT</p>
  </section>
</body>
</html>
```